VENTURE CAPITAL GROUP BUSINESS CARD DESIGN

Venture Capital Group based in SF looking for a bold business card design. No trendy colour explosion, 3D effects etc. Just "simple" optical effects. Works on your brain, keeps your eye focused and sticks to your mind.
Target Market(s)
Technology startups
Industry/Entity Type
Venture Capital
Contact Information for Business Card
DESMOND WHITLAKE
MANAGING PARTNER
187 FENWORTH ST SAN FRANCISCO, CA 94187
415.555.0142 O
415.555.0147 F
415.555.0193 C
desmond@veldtmoorcapital.ventures

```html
<!DOCTYPE html>
<html lang="en">
<head>
<meta charset="utf-8">
<title>Veldtmoor Capital Group – Business Card</title>
<link rel="stylesheet" href="https://fonts.googleapis.com/css2?family=Open+Sans:wght@400;600;700&display=swap">
<style>
  :root {
    --stage: #2b2b2b;
    --card-black: #050505;
    --green: #1f9a3c;
    --green-light: #3cc25a;
    --green-dark: #0c5a22;
    --white: #ffffff;
    --name-grey: #d9d9d9;
    --icon-grey: #7a7a7a;
  }
  * { margin: 0; padding: 0; box-sizing: border-box; }
  html, body {
    width: 1200px; height: 900px; overflow: hidden;
    background: var(--stage);
    font-family: "Open Sans", Arial, sans-serif;
  }
  .sheet {
    position: relative; width: 1200px; height: 900px;
    display: flex; flex-direction: column; align-items: center;
    justify-content: center; gap: 40px;
  }
  .card {
    position: relative; width: 660px; height: 377px;
    border-radius: 22px; overflow: hidden;
    background: var(--card-black);
  }
  .brand {
    position: absolute; display: flex; flex-direction: column; align-items: center;
  }
  .brand-dot {
    border-radius: 50%;
    background: var(--white);
  }
  .brand-name {
    color: var(--green); font-weight: 600; letter-spacing: 0.06em;
    text-transform: uppercase; white-space: nowrap;
  }
  /* front */
  .card-front .brand { left: 0; right: 0; top: 92px; }
  .card-front .brand-dot { width: 112px; height: 112px; margin-bottom: 22px; }
  .card-front .brand-name { font-size: 30px; }
  .card-front .brand-sub {
    color: var(--green); font-weight: 600; font-size: 11px;
    letter-spacing: 0.45em; text-transform: uppercase; margin-top: 4px;
  }
  /* back */
  .card-back .swoop { position: absolute; inset: 0; width: 100%; height: 100%; }
  .card-back .brand { right: 34px; top: 30px; }
  .card-back .brand-dot { width: 80px; height: 80px; margin-bottom: 12px; }
  .card-back .brand-name { font-size: 21px; }
  .card-back .brand-sub {
    color: var(--green); font-weight: 600; font-size: 8px;
    letter-spacing: 0.45em; text-transform: uppercase; margin-top: 3px;
  }
  .holder { position: absolute; left: 36px; top: 122px; }
  .holder-name {
    color: var(--name-grey); font-weight: 700; font-size: 25px;
    letter-spacing: 0.02em; line-height: 1.1;
  }
  .holder-title {
    color: var(--green-light); font-weight: 600; font-size: 14px;
    letter-spacing: 0.03em;
  }
  .contact {
    position: absolute; left: 40px; top: 270px;
    color: var(--green); font-size: 12.5px; font-weight: 600;
    line-height: 16px; list-style: none;
  }
  .contact li { display: flex; align-items: center; gap: 8px; }
  .contact .address { padding-left: 0; }
  .contact svg { width: 11px; height: 11px; flex: none; fill: var(--icon-grey); }
</style>
</head>
<body>
<main class="sheet">

  <section class="card card-front" aria-label="Card front">
    <div class="brand">
      <span class="brand-dot"></span>
      <span class="brand-name">Veldtmoor</span>
      <span class="brand-sub">Capital Group</span>
    </div>
  </section>

  <section class="card card-back" aria-label="Card back">
    <svg class="swoop" viewBox="0 0 660 377" preserveAspectRatio="none" aria-hidden="true">
      <defs>
        <linearGradient id="swoop-green" x1="0" y1="0" x2="1" y2="0">
          <stop offset="0" stop-color="#3cc25a"/>
          <stop offset="0.6" stop-color="#1f9a3c"/>
          <stop offset="1" stop-color="#0c5a22"/>
        </linearGradient>
      </defs>
      <path d="M0,212 C180,170 470,148 575,182 C645,212 610,320 525,377 L0,377 Z" fill="url(#swoop-green)"/>
      <path d="M0,262 C170,230 420,212 525,228 C580,244 566,322 485,377 L0,377 Z" fill="#ffffff"/>
    </svg>

    <div class="brand">
      <span class="brand-dot"></span>
      <span class="brand-name">Veldtmoor</span>
      <span class="brand-sub">Capital Group</span>
    </div>

    <div class="holder">
      <h1 class="holder-name">DESMOND WHITLAKE</h1>
      <p class="holder-title">MANAGING PARTNER</p>
    </div>

    <ul class="contact">
      <li class="address">187 FENWORTH ST SAN</li>
      <li class="address">FRANCISCO, CA 94187</li>
      <li>
        <svg viewBox="0 0 24 24" aria-label="Office"><path d="M6.6 10.8c1.4 2.8 3.8 5.1 6.6 6.6l2.2-2.2c.3-.3.7-.4 1-.2 1.1.4 2.3.6 3.6.6.6 0 1 .4 1 1V20c0 .6-.4 1-1 1C10.6 21 3 13.4 3 4c0-.6.4-1 1-1h3.5c.6 0 1 .4 1 1 0 1.2.2 2.4.6 3.6.1.3 0 .7-.2 1z"/></svg>
        415.555.0142
      </li>
      <li>
        <svg viewBox="0 0 24 24" aria-label="Fax"><path d="M7 2h10v6H7zM4 9h16a2 2 0 0 1 2 2v7h-4v4H6v-4H2v-7a2 2 0 0 1 2-2zm4 8v3h8v-3z"/></svg>
        415.555.0147
      </li>
      <li>
        <svg viewBox="0 0 24 24" aria-label="Mobile"><path d="M7 1h10a2 2 0 0 1 2 2v18a2 2 0 0 1-2 2H7a2 2 0 0 1-2-2V3a2 2 0 0 1 2-2zm0 3v15h10V4z"/></svg>
        415.555.0193
      </li>
      <li>
        <svg viewBox="0 0 24 24" aria-label="Email"><path d="M2 5h20v14H2zm2 2v.5l8 5 8-5V7zm0 3v7h16v-7l-8 5z"/></svg>
        desmond@veldtmoorcapital.ventures
      </li>
    </ul>
  </section>

</main>
</body>
</html>
```